Vorelan.com Personal Trainer/Fitness Website

I want a website to market my personal training/Outdoor Bootcamp Class services, as well as to ditribute nutrivex. I need a logo as well I included an address for the Harbor Gales 1975 logo. I'd like Vorelan in place of Harbor Gales, and in Black and white, just different enough so I can't get sued by the PBL.
https://www.pictofind.example/imgres?imgurl=http%3A%2F%2Fwww.darnell-quibury.example%2Fwp-content%2Fuploads%2F2014%2F01%2Fgales_logo4.jpg&imgrefurl=http%3A%2F%2Fwww.darnell-quibury.example%2Fpbl-logo-redesigns-harbor-gales%2F&docid=_qkwzR7TBAgXpL&tbnid=m4tpU8KdOXjnRP%3A&w=600&h=450&client=ms-android-carrier&bih=512&biw=360&ved=0ahUKEwiRtpgyp9HMAhUTwGMKHRPMBWMQMwg6KBQwFA&iact=mrc&uact=8.
It should be about 5 pages 1. home 2. about 3. Services 4. Blog/Videos and programs 5. Contact.
http://www.dorvinfitness.example.uk/ is a website I like the style of.

Target Market(s)

Seattle area

Industry/Entity Type

Fitness

Coding

Coded - Design and coding required

Number of Pages Required

4 page

Font styles to use
Serif
Sans Serif

Requirements
Must have
• A minimal look
Nice to have
• A logo similar to the 1975 Harbor Galewinds Logo, with a Small Milo Brandt ripping his shirt open(with a picture of the logo on his shirt, picture within picture) to turn into Ironjaw in the center. Skyline is black, Background and small figure white(with black logo on shirt)

```html
<!DOCTYPE html>
<html lang="en">
<head>
<meta charset="utf-8">
<title>Vorelan – Personal Training &amp; Outdoor Bootcamp</title>
<link rel="stylesheet" href="https://fonts.googleapis.com/css2?family=Lato:wght@400;700;900&family=Questrial&display=swap">
<style>
:root{
  --red:#c1272d;
  --red-deep:#a82228;
  --dark:#2b2a2a;
  --darker:#1f1e1e;
  --slate:#474747;
  --white:#ffffff;
  --ink:#222222;
  --muted:#555555;
  --rule:#cfcfcf;
}
*{box-sizing:border-box;margin:0;padding:0}
html,body{width:1200px;height:3309px;overflow:hidden}
body{position:relative;font-family:'Lato',sans-serif;color:var(--ink);background:var(--white)}
.section{position:absolute;left:0;width:1200px;overflow:hidden}
.abs{position:absolute}
.display{font-family:'Questrial',sans-serif;font-weight:400}

/* header */
.topbar{top:0;height:115px;background:var(--dark)}
.contact-line{display:flex;align-items:center;gap:12px;color:var(--white);font-size:18px}
.icon-ring{width:30px;height:30px;border-radius:50%;border:2px solid var(--red);display:flex;align-items:center;justify-content:center}
.social{display:flex;gap:14px}
.social span{width:16px;height:16px;border-radius:50%;background:var(--red)}
.trainer-btn{left:823px;top:55px;width:245px;height:46px;background:var(--red);border-radius:6px;color:var(--white);font-weight:700;font-size:19px;display:flex;align-items:center;justify-content:center;gap:12px;letter-spacing:.5px}
.navbar{top:115px;height:46px;background:var(--white)}
.nav-item{top:0;height:46px;line-height:46px;font-size:16px;color:var(--ink);text-transform:uppercase;transform:translateX(-50%);padding:0 16px}
.nav-item.active{background:var(--red);color:var(--white);left:159px;width:110px;text-align:center}
.brand-disc{left:528px;top:2px;width:144px;height:144px;border-radius:50%;background:var(--white);border:6px solid var(--dark);z-index:3}
.brand-name{left:0;width:1200px;top:116px;text-align:center;font-size:34px;line-height:40px;font-weight:900;color:var(--dark);z-index:4;letter-spacing:1px}

/* hero */
.hero{top:161px;height:397px;background:linear-gradient(100deg,#3f5d2c 0%,#6f8c45 35%,#9aa974 60%,#4d6a38 100%)}
.hero-title{left:132px;top:205px;color:var(--white);font-size:35px;line-height:44px;text-transform:uppercase}
.hero-btn{left:132px;top:313px;width:243px;height:47px;border:2px solid var(--white);border-radius:6px;background:rgba(0,0,0,.55);color:var(--white);font-weight:700;font-size:20px;display:flex;align-items:center;gap:14px;padding-left:4px}
.hero-btn .ph{width:37px;height:37px;background:var(--dark);border-radius:4px;display:flex;align-items:center;justify-content:center}
.slide-arrow{width:44px;height:44px;border-radius:50%;border:2px solid rgba(255,255,255,.85);display:flex;align-items:center;justify-content:center}

/* services */
.services{top:558px;height:512px;background:linear-gradient(180deg,var(--red-deep),var(--red) 60%,#b32329)}
.section-title{left:0;width:1200px;text-align:center;font-size:36px}
.rule{height:2px}
.rule-mark{height:6px;width:70px}
.lede{left:190px;width:820px;text-align:center;color:var(--white);font-size:15px;line-height:24px}
.service{width:300px;text-align:center;color:var(--white);transform:translateX(-50%)}
.service .disc{width:120px;height:120px;border-radius:50%;background:var(--dark);border:3px solid var(--white);margin:0 auto}
.service h3{font-size:22px;font-weight:900;margin-top:33px}
.service p{font-size:15px;line-height:24px;margin-top:4px}
.service a{display:inline-block;margin-top:16px;font-size:13px;font-weight:900;color:var(--white);text-decoration:underline}

/* about */
.about{top:1070px;height:441px;background:linear-gradient(110deg,#2a2a2a 0%,#333 45%,#4f5448 75%,#6b725c 100%)}
.portrait{left:132px;top:130px;width:250px;height:247px;background:linear-gradient(160deg,#d8d6d0,#8d8378 60%,#3a3533);border:3px solid var(--white)}
.about-head{left:426px;top:145px;font-size:28px;color:var(--white)}
.about-head em{font-style:normal;color:var(--red)}
.about-copy{left:426px;top:196px;width:540px;font-size:13.6px;line-height:17.5px;color:var(--white);font-weight:700}

/* programs */
.programs{top:1511px;height:419px;background:var(--white)}
.calendar{left:132px;top:122px;width:252px;box-shadow:0 4px 8px rgba(0,0,0,.25)}
.cal-head{height:38px;background:var(--red);display:flex;align-items:center;justify-content:space-between;color:var(--white);font-weight:700;font-size:20px}
.cal-head span.nav{width:26px;height:38px;background:var(--dark);display:flex;align-items:center;justify-content:center}
.calendar table{width:100%;border-collapse:collapse;font-size:15px;text-align:center;background:var(--white)}
.calendar th{font-size:11px;font-weight:400;color:var(--muted);height:22px}
.calendar td{height:35px;border:1px solid #e3e3e3}
.calendar td.hl{background:#111;color:var(--white)}
.event{left:435px;width:640px;display:flex;gap:20px}
.date-badge{width:55px;flex:none;text-align:center}
.date-badge .d{background:var(--red);color:var(--white);font-size:22px;height:32px;line-height:32px}
.date-badge .m{border:1px solid var(--red);color:var(--red);font-size:17px;height:24px;line-height:22px}
.event h4{font-size:18px;font-weight:900;color:var(--ink)}
.event p{font-size:14px;color:var(--ink);margin-top:6px}
.event .time{font-size:12px;color:var(--muted);margin-top:8px;display:flex;align-items:center;gap:8px}

/* amenities */
.amenities{top:1930px;height:437px;background:linear-gradient(180deg,#1b1b1b,#3c3c3c 50%,#2a2827)}
.amen-title{left:0;width:1200px;top:80px;text-align:center;color:var(--white);font-size:62px;letter-spacing:1px}
.amen-title span{background:var(--red);padding:0 10px}
.amen-sub{left:0;width:1200px;top:173px;text-align:center;color:var(--white);font-size:17.5px;font-weight:700;text-transform:uppercase}
.play{left:562px;top:212px;width:76px;height:76px;border-radius:50%;background:#111;border:2px solid #555;display:flex;align-items:center;justify-content:center}
.watch{left:530px;top:307px;width:143px;height:44px;background:var(--red);border-radius:6px;color:var(--white);font-size:18px;font-weight:700;display:flex;align-items:center;justify-content:center}

/* testimonials */
.testimonials{top:2367px;height:379px;background:var(--white)}
.testimonial{width:440px;display:flex;gap:18px}
.quote-disc{width:88px;height:88px;flex:none;border-radius:50%;background:var(--dark);border:4px solid #ddd;display:flex;align-items:center;justify-content:center;color:var(--red);font-size:54px;font-weight:900;line-height:1}
.testimonial p{font-size:12.5px;line-height:20px;color:var(--ink)}
.testimonial p a{color:var(--red);text-decoration:none}
.testimonial .name{color:var(--red);font-size:15px;margin-top:4px}
.round-arrow{width:40px;height:40px;border-radius:50%;display:flex;align-items:center;justify-content:center}

/* get started */
.start{top:2746px;height:259px;background:var(--slate)}
.start-line{display:flex;align-items:center;gap:14px;color:var(--white);font-size:18px}
.start-line .icon-ring{border-color:var(--white);width:40px;height:40px}
.notch{left:565px;top:3003px;width:0;height:0;border-left:17px solid transparent;border-right:17px solid transparent;border-top:18px solid var(--slate);z-index:2}

/* form */
.form-band{top:3005px;height:256px;background:var(--red)}
.field{background:var(--white);height:35px;font-size:13px;color:var(--ink);padding:8px 10px}
.send{left:765px;top:143px;width:146px;height:33px;background:var(--dark);color:var(--white);font-size:17px;display:flex;align-items:center;justify-content:center;letter-spacing:1px}

/* footer */
.footer{top:3261px;height:48px;background:var(--dark)}
.footer small{left:132px;top:17px;font-size:11px;color:#ddd}
</style>
</head>
<body>

<header class="section topbar">
  <div class="abs contact-line" style="left:132px;top:17px">
    <span class="icon-ring"><svg width="14" height="14" viewBox="0 0 24 24"><path fill="#fff" d="M6.6 10.8a15 15 0 0 0 6.6 6.6l2.2-2.2a1 1 0 0 1 1-.25 11.4 11.4 0 0 0 3.6.57 1 1 0 0 1 1 1V20a1 1 0 0 1-1 1A17 17 0 0 1 3 4a1 1 0 0 1 1-1h3.5a1 1 0 0 1 1 1 11.4 11.4 0 0 0 .57 3.6 1 1 0 0 1-.25 1z"/></svg></span>018.462.7305
  </div>
  <div class="abs contact-line" style="left:132px;top:62px">
    <span class="icon-ring"><svg width="14" height="14" viewBox="0 0 24 24"><path fill="#fff" d="M2 5h20v14H2z M2 5l10 8 10-8" stroke="#2b2a2a" stroke-width="1.5"/></svg></span>info@vorelan.com
  </div>
  <div class="abs social" style="left:950px;top:18px"><span></span><span></span><span></span><span></span></div>
  <div class="abs trainer-btn"><svg width="26" height="22" viewBox="0 0 26 22"><rect x="1" y="1" width="24" height="20" rx="4" fill="#fff"/></svg>FIND A TRAINER</div>
</header>

<nav class="section navbar" style="overflow:visible;z-index:2">
  <span class="abs nav-item active" style="transform:translateX(-50%)">Home</span>
  <span class="abs nav-item" style="left:280px">About Us</span>
  <span class="abs nav-item" style="left:417px">Services</span>
  <span class="abs nav-item" style="left:757px">Blog</span>
  <span class="abs nav-item" style="left:883px">Programs</span>
  <span class="abs nav-item" style="left:1028px">Contact</span>
</nav>
<div class="abs brand-disc"></div>
<div class="abs brand-name">VORELAN</div>

<section class="section hero" role="img" aria-label="Photo of a person stretching on a grass field">
  <h1 class="abs hero-title display">Get fit &amp; have fun<br>the way it should be</h1>
  <div class="abs hero-btn"><span class="ph"><svg width="18" height="18" viewBox="0 0 24 24"><path fill="#fff" d="M6.6 10.8a15 15 0 0 0 6.6 6.6l2.2-2.2a1 1 0 0 1 1-.25 11.4 11.4 0 0 0 3.6.57 1 1 0 0 1 1 1V20a1 1 0 0 1-1 1A17 17 0 0 1 3 4a1 1 0 0 1 1-1h3.5a1 1 0 0 1 1 1 11.4 11.4 0 0 0 .57 3.6 1 1 0 0 1-.25 1z"/></svg></span>CONTACT NOW</div>
  <div class="abs slide-arrow" style="left:29px;top:177px"><svg width="12" height="14" viewBox="0 0 12 14"><path d="M9 1 3 7l6 6" fill="none" stroke="#fff" stroke-width="2"/></svg></div>
  <div class="abs slide-arrow" style="left:1101px;top:177px"><svg width="12" height="14" viewBox="0 0 12 14"><path d="m3 1 6 6-6 6" fill="none" stroke="#fff" stroke-width="2"/></svg></div>
</section>

<section class="section services">
  <h2 class="abs section-title display" style="top:37px;color:var(--white)">OUR SERVICES</h2>
  <div class="abs rule" style="left:148px;top:88px;width:904px;background:rgba(255,255,255,.6)"></div>
  <div class="abs rule-mark" style="left:565px;top:86px;background:var(--dark)"></div>
  <p class="abs lede" style="top:122px">Lorem ipsum dolor sit amet, consectetur adipiscing elit. Morbi quis ante sed massa consectetur feugiat id at tellus. Fusce tristique dictum tincidunt. Nam viverra euismod pretium</p>
  <div class="abs service" style="left:265px;top:185px"><div class="disc" role="img" aria-label="Personal training icon"></div><h3>Personal Training</h3><p>Lorem ipsum dolor sit amet,<br>consectetur adipiscing elit.<br>Morbi quis ante sed.</p><a>Read More</a></div>
  <div class="abs service" style="left:600px;top:185px"><div class="disc" role="img" aria-label="Online coaching icon"></div><h3>Online Coaching</h3><p>Lorem ipsum dolor sit amet,<br>consectetur adipiscing elit.<br>Morbi quis ante sed.</p><a>Read More</a></div>
  <div class="abs service" style="left:935px;top:185px"><div class="disc" role="img" aria-label="Outdoor bootcamp icon"></div><h3>Outdoor Bootcamp</h3><p>Lorem ipsum dolor sit amet,<br>consectetur adipiscing elit.<br>Morbi quis ante sed.</p><a>Read More</a></div>
</section>

<section class="section about" role="img" aria-label="Background photo of people training outdoors">
  <h2 class="abs display" style="left:137px;top:24px;font-size:35px;color:var(--white)">About Us</h2>
  <div class="abs rule" style="left:132px;top:84px;width:578px;background:var(--red)"></div>
  <div class="abs portrait" role="img" aria-label="Portrait photo of the trainer"></div>
  <h3 class="abs about-head display"><em>Motivation, Consistency</em> &amp; Intensity</h3>
  <p class="abs about-copy">Lorem ipsum dolor sit amet, consectetur adipiscing elit. Sed vitae magna tellus. Aenean ante nunc, semper nec cursus non, rutrum ac eros. Vestibulum mattis justo ac dui bibendum consequat a ac ipsum. Praesent a arcu venenatis, auctor velit eu, suscipit libero. Quisque convallis, leo ac pharetra sagittis, ipsum arcu auctor urna, sit amet cursus risus augue in eros. Duis lacinia nisi vitae leo commodo, non finibus magna maximus. Sed posuere, neque eget bibendum pulvinar, ligula erat suscipit dolor, ut maximus arcu mi et tortor. Quisque imperdiet turpis et ligula mollis ultricies. Mauris lacinia rhoncus odio, at rutrum diam mollis eu.</p>
</section>

<section class="section programs">
  <h2 class="abs section-title display" style="top:43px;font-size:33px">Our Programs</h2>
  <div class="abs rule" style="left:132px;top:93px;width:936px;background:var(--rule)"></div>
  <div class="abs calendar">
    <div class="cal-head"><span class="nav">&#8249;</span>MAY 2016<span class="nav">&#8250;</span></div>
    <table>
      <tr><th>SUN</th><th>MON</th><th>TUE</th><th>WED</th><th>THU</th><th>FRI</th><th>SAT</th></tr>
      <tr><td></td><td>1</td><td class="hl">2</td><td>3</td><td>4</td><td>5</td><td>6</td></tr>
      <tr><td>7</td><td>8</td><td>9</td><td>10</td><td>11</td><td class="hl">12</td><td>13</td></tr>
      <tr><td>14</td><td>15</td><td class="hl">16</td><td>17</td><td>18</td><td>19</td><td>20</td></tr>
      <tr><td>21</td><td>22</td><td>23</td><td>24</td><td>25</td><td>26</td><td>27</td></tr>
      <tr><td>28</td><td>29</td><td>30</td><td>31</td><td></td><td></td><td></td></tr>
    </table>
  </div>
  <div class="abs event" style="top:122px"><div class="date-badge"><div class="d">02</div><div class="m">MAY</div></div><div><h4>Lorem ipsum dolor sit amet, consectetur adipiscing</h4><p>Lorem ipsum dolor sit amet, consectetur adipiscing elit. Sed vitae magna tellus.</p><div class="time"><svg width="12" height="12" viewBox="0 0 12 12"><circle cx="6" cy="6" r="5" fill="none" stroke="#555"/><path d="M6 3v3h2" fill="none" stroke="#555"/></svg>07:00 am</div></div></div>
  <div class="abs event" style="top:206px"><div class="date-badge"><div class="d">12</div><div class="m">MAY</div></div><div><h4>Lorem ipsum dolor sit amet, consectetur adipiscing</h4><p>Lorem ipsum dolor sit amet, consectetur adipiscing elit. Sed vitae magna tellus.</p><div class="time"><svg width="12" height="12" viewBox="0 0 12 12"><circle cx="6" cy="6" r="5" fill="none" stroke="#555"/><path d="M6 3v3h2" fill="none" stroke="#555"/></svg>08:00 am</div></div></div>
  <div class="abs event" style="top:290px"><div class="date-badge"><div class="d">16</div><div class="m">MAY</div></div><div><h4>Lorem ipsum dolor sit amet, consectetur adipiscing</h4><p>Lorem ipsum dolor sit amet, consectetur adipiscing elit. Sed vitae magna tellus.</p><div class="time"><svg width="12" height="12" viewBox="0 0 12 12"><circle cx="6" cy="6" r="5" fill="none" stroke="#555"/><path d="M6 3v3h2" fill="none" stroke="#555"/></svg>07:30 am</div></div></div>
</section>

<section class="section amenities" role="img" aria-label="Photo of a gym floor with exercise machines">
  <h2 class="abs amen-title display">STATE OF THE ART <span>AMENITIES</span></h2>
  <p class="abs amen-sub">Lorem ipsum dolor sit amet consectetur adipiscing elit sed vitae magna tellus</p>
  <div class="abs play"><svg width="24" height="28" viewBox="0 0 24 28"><path d="M3 2l19 12L3 26z" fill="#fff"/></svg></div>
  <div class="abs watch">Watch Video</div>
</section>

<section class="section testimonials">
  <h2 class="abs section-title display" style="top:48px;font-size:33px">CLIENT <span style="color:var(--red)">TESTIMONIALS</span></h2>
  <div class="abs rule" style="left:132px;top:93px;width:936px;background:var(--rule)"></div>
  <div class="abs round-arrow" style="left:53px;top:210px;border:1px solid #ccc"><svg width="10" height="14" viewBox="0 0 10 14"><path d="M8 1 2 7l6 6" fill="none" stroke="#999" stroke-width="2"/></svg></div>
  <div class="abs round-arrow" style="left:1107px;top:210px;background:var(--dark)"><svg width="10" height="14" viewBox="0 0 10 14"><path d="m2 1 6 6-6 6" fill="none" stroke="#fff" stroke-width="2"/></svg></div>
  <div class="abs testimonial" style="left:132px;top:122px"><div class="quote-disc">&#8220;</div><div><p>Lorem ipsum dolor sit amet, consectetur adipiscing elit. Sed vitae magna tellus. Aenean ante nunc, semper nec cursus non, rutrum ac eros. Vestibulum mattis justo... <a>Read More</a></p><div class="name">Renna Dalmore Quist</div></div></div>
  <div class="abs testimonial" style="left:633px;top:122px"><div class="quote-disc">&#8220;</div><div><p>Lorem ipsum dolor sit amet, consectetur adipiscing elit. Sed vitae magna tellus. Aenean ante nunc, semper nec cursus non, rutrum ac eros. Vestibulum mattis justo... <a>Read More</a></p><div class="name">Tova Brisk</div></div></div>
  <div class="abs testimonial" style="left:132px;top:250px"><div class="quote-disc">&#8220;</div><div><p>Lorem ipsum dolor sit amet, consectetur adipiscing elit. Sed vitae magna tellus. Aenean ante nunc, semper nec cursus non, rutrum ac eros. Vestibulum mattis justo... <a>Read More</a></p><div class="name">Kenzo</div></div></div>
  <div class="abs testimonial" style="left:633px;top:250px"><div class="quote-disc">&#8220;</div><div><p>Lorem ipsum dolor sit amet, consectetur adipiscing elit. Sed vitae magna tellus. Aenean ante nunc, semper nec cursus non, rutrum ac eros. Vestibulum mattis justo... <a>Read More</a></p><div class="name">Emil</div></div></div>
</section>

<section class="section start">
  <h2 class="abs section-title display" style="top:30px;font-size:31px;color:var(--white)">LET'S GET STARTED</h2>
  <div class="abs rule" style="left:132px;top:86px;width:936px;background:rgba(255,255,255,.35)"></div>
  <p class="abs" style="left:0;width:1200px;top:110px;text-align:center;color:var(--white);font-size:21px">Thank you for your interest in contacting VORELAN</p>
  <div class="abs start-line" style="left:234px;top:168px"><span class="icon-ring"><svg width="14" height="18" viewBox="0 0 14 18"><path d="M7 1a6 6 0 0 1 6 6c0 4.5-6 10-6 10S1 11.5 1 7a6 6 0 0 1 6-6z" fill="#fff"/><circle cx="7" cy="7" r="2" fill="#474747"/></svg></span><span>Lorem ipsum dolor sit<br>amet - 12345</span></div>
  <div class="abs start-line" style="left:556px;top:168px"><span class="icon-ring"><svg width="16" height="16" viewBox="0 0 24 24"><path fill="#fff" d="M6.6 10.8a15 15 0 0 0 6.6 6.6l2.2-2.2a1 1 0 0 1 1-.25 11.4 11.4 0 0 0 3.6.57 1 1 0 0 1 1 1V20a1 1 0 0 1-1 1A17 17 0 0 1 3 4a1 1 0 0 1 1-1h3.5a1 1 0 0 1 1 1 11.4 11.4 0 0 0 .57 3.6 1 1 0 0 1-.25 1z"/></svg></span>018.462.7305</div>
  <div class="abs start-line" style="left:785px;top:168px"><span class="icon-ring"><svg width="16" height="12" viewBox="0 0 16 12"><rect x="0.5" y="0.5" width="15" height="11" fill="#fff"/><path d="M1 1l7 6 7-6" fill="none" stroke="#474747"/></svg></span>info@vorelan.com</div>
</section>
<div class="abs notch"></div>

<section class="section form-band">
  <h2 class="abs" style="left:0;width:1200px;top:33px;text-align:center;color:var(--white);font-size:23px;font-weight:400">Please Fill Out The Form Below</h2>
  <div class="abs field" style="left:141px;top:95px;width:294px">Your Name</div>
  <div class="abs field" style="left:452px;top:95px;width:294px">Email</div>
  <div class="abs field" style="left:765px;top:95px;width:294px">Phone</div>
  <div class="abs field" style="left:141px;top:141px;width:605px;height:73px">Comments</div>
  <div class="abs send">SEND</div>
</section>

<footer class="section footer">
  <small class="abs">Copyright © 2016 VORELAN. All Rights Reserved.</small>
  <div class="abs social" style="left:950px;top:16px"><span style="background:#888"></span><span style="background:#888"></span><span style="background:#888"></span><span style="background:#888"></span></div>
</footer>

</body>
</html>
```